Landing Page / Waitlist

I would like a landing page for people to sign up for a waiting list. The text on the page should include (but is not limited to):
1) Main point: The accounting system you'll love
2) Secondary points:
a. Ruthlessly efficient
b. Quietly intelligent
c. Driven by AI
I've attached a file of our logo

The design should be simple, clean, and innovative - this is an ai company

```html
<!DOCTYPE html>
<html lang="en">
<head>
<meta charset="UTF-8">
<title>Ledgerly — Join the Waitlist</title>
<link href="https://fonts.googleapis.com/css2?family=Montserrat:wght@600;700;800&family=Lato:wght@400;700&display=swap" rel="stylesheet">
<style>
  :root {
    --bg-deep: #02070d;
    --bg-navy: #061a2c;
    --glow-blue: #0b4f7c;
    --glow-teal: #0e6e86;
    --accent: #00a6f5;
    --white: #ffffff;
    --field-text: #6b6b6b;
    --rule: rgba(255, 255, 255, 0.45);
  }
  * { box-sizing: border-box; margin: 0; padding: 0; }
  html, body {
    width: 1200px;
    height: 729px;
    overflow: hidden;
    background: var(--bg-deep);
  }
  .page {
    position: relative;
    width: 1200px;
    height: 729px;
    overflow: hidden;
    color: var(--white);
    font-family: 'Lato', Arial, sans-serif;
  }
  .backdrop {
    position: absolute;
    inset: 0;
    background:
      radial-gradient(ellipse 420px 340px at 1080px 560px, rgba(14, 110, 134, 0.45), transparent 70%),
      radial-gradient(ellipse 360px 300px at 120px 160px, rgba(11, 79, 124, 0.45), transparent 70%),
      radial-gradient(ellipse 500px 260px at 1150px 120px, rgba(11, 79, 124, 0.35), transparent 70%),
      linear-gradient(160deg, var(--bg-deep) 0%, var(--bg-navy) 55%, var(--bg-deep) 100%);
  }
  .brand {
    position: absolute;
    top: 178px;
    left: 0;
    width: 1200px;
    display: flex;
    justify-content: center;
    align-items: center;
    gap: 14px;
  }
  .brand-dot {
    width: 26px;
    height: 26px;
    background: var(--accent);
  }
  .brand-name {
    font-family: 'Montserrat', Arial, sans-serif;
    font-weight: 700;
    font-size: 50px;
    letter-spacing: -1px;
    color: var(--white);
  }
  .headline {
    position: absolute;
    top: 314px;
    left: 0;
    width: 1200px;
    text-align: center;
    font-family: 'Montserrat', Arial, sans-serif;
    font-weight: 800;
    font-size: 53px;
    letter-spacing: 0.3px;
  }
  .waitlist-form {
    position: absolute;
    top: 430px;
    left: 299px;
    display: flex;
    align-items: flex-start;
    gap: 15px;
  }
  .email-field {
    width: 403px;
    height: 47px;
    margin-top: 4px;
    background: var(--white);
    border: none;
    padding: 0 26px 4px;
    font-family: 'Lato', Arial, sans-serif;
    font-size: 15px;
    color: var(--field-text);
    display: flex;
    align-items: center;
  }
  .join-button {
    width: 181px;
    height: 47px;
    background: var(--accent);
    border: none;
    color: var(--white);
    font-family: 'Lato', Arial, sans-serif;
    font-weight: 700;
    font-size: 17px;
  }
  .features {
    position: absolute;
    top: 544px;
    left: 0;
    width: 1200px;
    list-style: none;
  }
  .feature {
    position: absolute;
    top: 0;
    display: flex;
    align-items: center;
    gap: 10px;
    font-family: 'Montserrat', Arial, sans-serif;
    font-weight: 700;
    font-size: 17px;
  }
  .feature:nth-child(1) { left: 242px; }
  .feature:nth-child(2) { left: 499px; }
  .feature:nth-child(3) { left: 756px; }
  .feature-icon { width: 18px; height: 18px; flex: none; }
  .footer {
    position: absolute;
    top: 678px;
    left: 112px;
    width: 977px;
    border-top: 1px solid var(--rule);
    padding-top: 13px;
    display: flex;
    justify-content: space-between;
    font-size: 15px;
  }
  .footer a { color: var(--white); text-decoration: none; }
</style>
</head>
<body>
<main class="page">
  <div class="backdrop" role="img" aria-label="Dark navy background with glowing blue circuit-board traces in the corners"></div>

  <div class="brand">
    <span class="brand-dot"></span>
    <span class="brand-name">Ledgerly</span>
  </div>

  <h1 class="headline">The Accounting System You’ll Love</h1>

  <form class="waitlist-form">
    <div class="email-field">Email Address</div>
    <button class="join-button" type="button">Join the Waitlist</button>
  </form>

  <ul class="features">
    <li class="feature">
      <svg class="feature-icon" viewBox="0 0 18 18"><circle cx="9" cy="9" r="9" fill="#00a6f5"/><path d="M4.5 9h8M9.5 6l3 3-3 3" stroke="#02070d" stroke-width="1.6" fill="none" stroke-linecap="round" stroke-linejoin="round"/></svg>
      Ruthlessly Efficient
    </li>
    <li class="feature">
      <svg class="feature-icon" viewBox="0 0 18 18"><circle cx="9" cy="9" r="9" fill="#00a6f5"/><path d="M4.5 9h8M9.5 6l3 3-3 3" stroke="#02070d" stroke-width="1.6" fill="none" stroke-linecap="round" stroke-linejoin="round"/></svg>
      Quietly Intelligent
    </li>
    <li class="feature">
      <svg class="feature-icon" viewBox="0 0 18 18"><circle cx="9" cy="9" r="9" fill="#00a6f5"/><path d="M4.5 9h8M9.5 6l3 3-3 3" stroke="#02070d" stroke-width="1.6" fill="none" stroke-linecap="round" stroke-linejoin="round"/></svg>
      Driven by AI
    </li>
  </ul>

  <footer class="footer">
    <nav><a href="#">Privacy Policy</a> | <a href="#">Terms</a> | <a href="#">Contact</a></nav>
    <span>© 2025 Ledgerly — All rights reserved.</span>
  </footer>
</main>
</body>
</html>
```